K & R Acre Works. Business card design

We need a business card designed for a new business. We have a bulldozer and tractor service. We clear land and make wildlife food plots. We provide disking, bush hogging, and site prep services.
I have attached an image of a business card that I like and would like my business cards to look similar.

Target Market(s)

anyone needing bulldozer and/or tractor services

Industry/Entity Type

Business

Contact Information for Business Card

K & R Acre Works, Operated by 7-T-Ranch
Wade Colton
601-472-3358
wcr4817@fieldmail-example.com

Font styles to use
Sans Serif

Colors

Designer to choose colors to be used in the design.

Requirements
Must have
• image of tractor and bulldozer
• Land Clearing
• Wildlife food plots
• Bush Hogging
• Disking
• Site prep
Nice to have
• i have included a image of a business card that i like. I would like mine to be similar.

```html
<!DOCTYPE html>
<html lang="en">
<head>
<meta charset="UTF-8">
<title>K &amp; R Acre Works – Business Card</title>
<link rel="stylesheet" href="https://fonts.googleapis.com/css2?family=Roboto:wght@400;500&family=Roboto+Condensed:wght@500;700&display=swap">
<style>
  :root {
    --stage: #2e2e2e;
    --card: #f2f2f0;
    --olive: #938d2e;
    --olive-band: #9a9332;
    --brown: #5c3513;
    --ink: #3f3f3f;
    --white: #ffffff;
  }
  * { margin: 0; padding: 0; box-sizing: border-box; }
  html, body {
    width: 1200px; height: 960px; overflow: hidden;
    background: var(--stage);
  }
  .card {
    position: absolute; left: 300px; top: 309px;
    width: 600px; height: 342px;
    background: var(--card);
    font-family: "Roboto", sans-serif;
  }
  .brand {
    position: absolute; left: 323px; top: 31px; width: 247px;
  }
  .brand-name {
    display: block;
    font-family: "Roboto Condensed", sans-serif;
    font-weight: 700; font-size: 21px; line-height: 25px;
    color: var(--brown); letter-spacing: 0.3px;
    white-space: nowrap;
  }
  .brand-tagline {
    display: block;
    font-family: "Roboto Condensed", sans-serif;
    font-weight: 700; font-size: 10.5px; line-height: 13px;
    color: var(--ink); white-space: nowrap;
  }
  .photo {
    position: absolute; top: 71px; height: 80px;
  }
  .photo-dozer {
    left: 323px; width: 134px;
    background: linear-gradient(180deg, #7f8a6a 0%, #c9b843 45%, #6a5d48 75%, #8a8270 100%);
  }
  .photo-tractor {
    left: 462px; width: 108px;
    background: linear-gradient(180deg, #7c8a55 0%, #b6562f 50%, #a39166 100%);
  }
  .person {
    position: absolute; left: 30px; top: 176px;
  }
  .person-name {
    font-family: "Roboto Condensed", sans-serif;
    font-weight: 500; font-size: 21px; line-height: 24px;
    color: var(--olive);
  }
  .person-role {
    font-family: "Roboto", sans-serif;
    font-weight: 400; font-size: 15px; line-height: 18px;
    color: var(--brown);
  }
  .services {
    position: absolute; left: 30px; top: 226px;
  }
  .services-heading {
    font-family: "Roboto Condensed", sans-serif;
    font-weight: 500; font-size: 17px; line-height: 20px;
    color: var(--olive); margin-bottom: 2px;
  }
  .services-row {
    font-size: 14.5px; line-height: 18px; color: var(--ink);
    white-space: nowrap;
  }
  .services-row .dot { color: var(--olive); font-size: 12px; }
  .contact-band {
    position: absolute; left: 0; bottom: 0;
    width: 600px; height: 41px;
    background: var(--olive-band);
    color: var(--white);
    font-size: 13.5px; line-height: 41px;
    padding-left: 29px; white-space: nowrap; overflow: hidden;
  }
  .contact-band b { font-weight: 500; }
</style>
</head>
<body>
  <div class="card">
    <div class="brand">
      <span class="brand-name">K &amp; R ACRE WORKS</span>
      <span class="brand-tagline">OPERATED BY 7-T-RANCH • LAND IMPROVEMENT</span>
    </div>
    <div class="photo photo-dozer" role="img" aria-label="Photo of a yellow bulldozer pushing soil on a cleared site"></div>
    <div class="photo photo-tractor" role="img" aria-label="Photo of an orange tractor with a front loader in a field"></div>

    <div class="person">
      <div class="person-name">WADE COLTON</div>
      <div class="person-role">OWNER</div>
    </div>

    <div class="services">
      <div class="services-heading">WE CREATE</div>
      <div class="services-row"><span class="dot">●</span> Land Clearing <span class="dot">●</span> Wildlife food plots</div>
      <div class="services-row"><span class="dot">●</span> Bush Hogging <span class="dot">●</span> Disking <span class="dot">●</span> Site prep</div>
    </div>

    <div class="contact-band">
      <b>P.</b> 601-472-3358 <b>E.</b>&nbsp; wcr4817@fieldmail-example.com <b>W.</b>&nbsp; kracreworks-example.com
    </div>
  </div>
</body>
</html>
```